Wine Bottle Label for Tall Fern Wines

We are a small, newly established winery in need of an original, bold and outstanding bottle label design for our Tall Fern wine.

Our vineyard and winery are located on a 200 acre farm in a remote part of southern Oregon. The name "Tall Fern" was inspired by the large, overgrown size of all of the foliage here, including our grapevines. Things grow large and vigorous in Oregon! And everything is very lush and green. It is almost surreal or other-worldly, like the landscapes seen in the Keeper of The Stones movies, or the land of Quill. It is a place that makes you say "wow" with its epic, large scale, natural beauty.

The name "Tall Fern" also captures the essence of our wine. It is big in flavor, quality and color. Our first release is a Pinot Noir (red). Pinot Noir wines often are subtle in flavor and thin in their color. Our label should convey that our Pinot Noir is a much more robust, darker, heavier, meatier, more flavorful wine that is a lot more fun than an "ordinary" wine. At the same time, this wine is not cheap, and so nothing in the label should convey "bargain," "low price," or "cheapness." This is a fine wine with a sense of adventure. Be sure to convey "quality" with your design along with "big," "adventure" and "fun".

The label should appeal to a younger demographic, both male and female, between the ages of 21 and 35. It should be non-traditional and adventurous and suggest a pushing of boundaries and a breaking of rules. This Pinot Noir does not conform to the normal "limitations" of the variety, therefore the label should not conform. It should have an "organic" or "natural" or "agricultural" vibe, as opposed to something mechanical or technical. It should, however, be contemporary. Do not confuse "natural" or "organic" with being nostalgic or old school. Think "agri-hipsters."

The label should be designed to fit on a Burgundy-style wine bottle (photo attached for reference). (Note: All Pinot Noir and Chardonnay is bottled in Burgundy bottles, If you are not sure about the bottle shape you can go to a local store and compare the various bottles. Locate a bottle of Pinot Noir or Chardonnay or anything identified as a "Burgundy Wine," and it should be the correct bottle. The tall, skinny bottles used for Cabernet Sauvignon are NOT correct)). Please see the "Must Have" notes for more on the bottle.

In summary, the final project should be a wine bottle label design that conveys bigness, vastness, adventurous, non-traditional, high quality wine. A good tagline to keep in mind is "Living Large."

Target Market(s)

Young, hip, non-conformist wine drinkers aged 21-35 with a sense of adventure and an appreciation of quality.

Industry/Entity Type

School

Requirements
Must have
• *Must contain the words:

Tall Fern (the brand)
2013 Pinot Noir (the vintage year and variety)

*The label must be designed to fit a Burgundy-style wine bottle. A photo is attached for reference.

*Additionally, the label needs to fit on the lower, widest part of the bottle. The label will be printed on sticky paper and rolled onto the bottle with a machine. The machine cannot apply labels to the neck of the bottle. The maximum size of a label that will fit this space is 5.5 inches wide by 4.5 inches tall. You DO NOT have to fill ALL of this space or confine the label shape to a rectangle, but the label cannot exceed this size or it won't stick to the bottle properly. It will really help if you can put your hands on an actual bottle to see the logistics of applying the label. But if that is not possible, just do your best with the instructions you have. I am confident the winning design could be adjusted to fit the bottle, if necessary
Nice to have
• *Wine grape leaf or leaves.

*A concept I have been playing with is sunlight shining through leaves like light through a Marlowe lamp or a stained glass window. This is NOT a requirement for this label. However, if the concept inspires and idea, I would be most happy to see it.
Should not have
• IF a leaf or leaves are included in the design (not a requirement) they MUST be wine grapevine leafs and preferably leaves of the Pinot Noir vine. Do not use generic leaves or identifiable leaves such as oak leaves, maple leaves, or anything that looks like the Canadian flag or the Halden Ridge Ravens hockey logo. Reference the attached photos of wine grape leaves to see the correct leaf type. I am happy to email more photos upon request. These photos may be used in whole or in part in your design, however, a leaf from a photo is NOT a requirement, nor is the image of a leaf or leaves.

This label should NOT be designed for Bordeaux-style wine bottles (the tall, skinny ones).

```html
<!DOCTYPE html>
<html lang="en">
<head>
<meta charset="utf-8">
<title>Tall Fern 2013 Pinot Noir Label</title>
<link rel="stylesheet" href="https://fonts.googleapis.com/css2?family=Raleway:ital,wght@0,200;0,300;1,300&display=swap">
<style>
  :root {
    --ink-black: #0b0508;
    --deep-plum: #24101a;
    --wine: #7b3b56;
    --wine-light: #8a4563;
    --wine-shadow: #3a1827;
    --silver: #d9d8d0;
    --pearl: #ececec;
    --leaf-bright: #8fd13a;
    --leaf-mid: #4e9a1e;
    --leaf-deep: #1f4d0c;
    --leaf-glow: rgba(225, 235, 200, 0.55);
  }
  * { margin: 0; padding: 0; box-sizing: border-box; }
  html, body { width: 1200px; height: 592px; overflow: hidden; background: var(--ink-black); }
  .label {
    position: relative;
    width: 1200px;
    height: 592px;
    overflow: hidden;
    font-family: "Raleway", "Helvetica Neue", Arial, sans-serif;
    background:
      radial-gradient(ellipse 520px 420px at 0% 100%, var(--ink-black) 20%, transparent 75%),
      linear-gradient(100deg,
        var(--ink-black) 0%,
        var(--deep-plum) 30%,
        var(--wine-shadow) 38%,
        var(--wine) 45%,
        var(--wine-light) 50%,
        var(--deep-plum) 58%,
        var(--ink-black) 62%,
        var(--wine-shadow) 68%,
        var(--wine) 76%,
        var(--wine-light) 88%,
        var(--wine) 100%);
  }
  .vine-leaf {
    position: absolute;
    left: 0;
    top: 0;
    width: 420px;
    height: 360px;
  }
  .brand-name {
    position: absolute;
    left: 628px;
    top: 150px;
    font-size: 150px;
    font-weight: 200;
    letter-spacing: -2px;
    line-height: 1;
    color: var(--silver);
    white-space: nowrap;
  }
  .vintage {
    position: absolute;
    left: 55px;
    top: 488px;
    font-size: 50px;
    font-weight: 300;
    letter-spacing: -1px;
    color: var(--pearl);
    text-shadow: 0 0 10px rgba(255, 255, 255, 0.35);
    white-space: nowrap;
  }
  .vintage .variety { font-style: italic; }
</style>
</head>
<body>
  <main class="label">
    <svg class="vine-leaf" viewBox="0 0 420 360" role="img" aria-label="Photograph of a bright green grapevine leaf with a soft pale glow">
      <defs>
        <radialGradient id="leafHalo" cx="50%" cy="45%" r="55%">
          <stop offset="55%" stop-color="var(--leaf-glow)"/>
          <stop offset="100%" stop-color="rgba(225,235,200,0)"/>
        </radialGradient>
        <radialGradient id="leafFill" cx="45%" cy="35%" r="65%">
          <stop offset="0%" stop-color="var(--leaf-bright)"/>
          <stop offset="60%" stop-color="var(--leaf-mid)"/>
          <stop offset="100%" stop-color="var(--leaf-deep)"/>
        </radialGradient>
      </defs>
      <ellipse cx="205" cy="170" rx="215" ry="185" fill="url(#leafHalo)"/>
      <ellipse cx="205" cy="165" rx="195" ry="160" fill="url(#leafFill)"/>
    </svg>

    <h1 class="brand-name">TallFern</h1>

    <p class="vintage">2013 <span class="variety">Pinot Noir</span></p>
  </main>
</body>
</html>
```